Dovecote Realty

Business cards for 4 people

They need to say for all
87 Tarrow Quay, Boston MA 02114

Each person will have their own personal information
We would like gold embossing for the name of the company
Marla is the blonde sitting in the chair smiling her information should be on the back of the card with her name and information
Should say for slogan classic pattern, elevated experience
grace@dovecoteprops.com
(413) 555-0182

Odette is the brunette with wavy hair in the tan suit odette@dovecoteprops.com
(617) 555-0137

faith@dovecoteprops.com
(413) 555-0164
standing next to the chair

hope@dovecoteprops.com
(413) 555-0199
close up headshot

```html
<!DOCTYPE html>
<html lang="en">
<head>
<meta charset="utf-8">
<title>Dovecote Realty – Business Cards</title>
<link rel="stylesheet" href="https://fonts.googleapis.com/css2?family=Playfair+Display:wght@800&family=Montserrat:wght@400&display=swap">
<style>
  :root {
    --backdrop: #1b1b1d;
    --navy: #223356;
    --gold: #e9b562;
    --ink-light: #f1f1f3;
    --ink-dark: #1f2c4c;
    --suit-light: #9a6f48;
    --suit-dark: #6a472c;
  }
  * { margin: 0; padding: 0; box-sizing: border-box; }
  html, body { width: 1200px; height: 1059px; overflow: hidden; background: var(--backdrop); }
  .sheet { position: relative; width: 1200px; height: 1059px; }

  .card {
    position: absolute;
    left: 255px;
    width: 690px;
    height: 392px;
    background: var(--navy);
    border-radius: 22px;
    overflow: hidden;
  }
  .card--front { top: 89px; }
  .card--back { top: 547px; }

  /* Company name set as plain text */
  .company {
    position: absolute;
    font-family: "Playfair Display", serif;
    font-weight: 800;
    color: var(--gold);
    line-height: 1;
    white-space: nowrap;
  }
  .card--front .company { left: 39px; top: 118px; font-size: 26px; letter-spacing: 0.5px; }
  .card--back .company { left: 0; right: 0; top: 170px; text-align: center; font-size: 48px; letter-spacing: 1px; }

  /* Name band */
  .name-band {
    position: absolute; left: 0; top: 177px; width: 530px; height: 58px;
    background: var(--gold); padding: 8px 0 0 39px;
  }
  .name-band__name {
    font-family: "Playfair Display", serif; font-weight: 800;
    font-size: 22px; letter-spacing: 0.5px; color: var(--ink-dark); line-height: 1.05;
  }
  .name-band__title {
    font-family: "Montserrat", sans-serif; font-size: 15px; color: var(--ink-light);
    margin-top: 3px; letter-spacing: 0.3px;
  }

  /* Contacts */
  .contacts { position: absolute; left: 39px; top: 256px; list-style: none; }
  .contacts__item {
    display: flex; align-items: center; gap: 7px; height: 25.3px;
    font-family: "Montserrat", sans-serif; font-size: 16px; color: var(--ink-light); letter-spacing: 0.3px;
  }
  .contacts__icon { width: 13px; height: 13px; flex: none; }

  /* Portrait area */
  .portrait {
    position: absolute; left: 466px; top: 21px; width: 190px; height: 371px;
    background: linear-gradient(180deg, var(--suit-light) 0%, var(--suit-dark) 100%);
    border-radius: 60px 60px 0 0;
  }
</style>
</head>
<body>
<main class="sheet">

  <section class="card card--front">
    <p class="company">Dovecote Realty</p>

    <div class="name-band">
      <p class="name-band__name">ODETTE VARNELL</p>
      <p class="name-band__title">Real Estate Advisor and Rentals Manager</p>
    </div>

    <ul class="contacts">
      <li class="contacts__item">
        <svg class="contacts__icon" viewBox="0 0 24 24"><path fill="#e9b562" d="M6.6 10.8a15.1 15.1 0 0 0 6.6 6.6l2.2-2.2a1 1 0 0 1 1-.25 11.4 11.4 0 0 0 3.6.57 1 1 0 0 1 1 1V20a1 1 0 0 1-1 1A17 17 0 0 1 3 4a1 1 0 0 1 1-1h3.5a1 1 0 0 1 1 1c0 1.25.2 2.45.57 3.57a1 1 0 0 1-.25 1z"/></svg>
        (617) 555-0137
      </li>
      <li class="contacts__item">
        <svg class="contacts__icon" viewBox="0 0 24 24"><path fill="#e9b562" d="M2 9l10-7 10 7v12H2z"/><path fill="none" stroke="#223356" stroke-width="1.4" d="M3 10l9 6 9-6"/></svg>
        odette@dovecoteprops.com
      </li>
      <li class="contacts__item">
        <svg class="contacts__icon" viewBox="0 0 24 24"><circle cx="12" cy="12" r="10" fill="#e9b562"/><path fill="#223356" d="M7 6c2 1 3 3 2 5s-3 1-4 3c-1-3 0-6 2-8zm8 5c2 0 3 2 2 4s-2 3-3 2 0-3-1-4 0-2 2-2z"/></svg>
        www.dovecoteprops.com
      </li>
      <li class="contacts__item">
        <svg class="contacts__icon" viewBox="0 0 24 24"><path fill="#e9b562" d="M12 1a8 8 0 0 0-8 8c0 6 8 14 8 14s8-8 8-14a8 8 0 0 0-8-8zm0 11a3 3 0 1 1 0-6 3 3 0 0 1 0 6z"/></svg>
        87 Tarrow Quay, Boston MA 02114
      </li>
    </ul>

    <div class="portrait" role="img" aria-label="Photo of the advisor in a tan suit, seated on a wooden chair"></div>
  </section>

  <section class="card card--back">
    <p class="company">Dovecote Realty</p>
  </section>

</main>
</body>
</html>
```